Web Design Project - Shipping Industry

Goals and Objectives
The objective of the new website is to create a more modern look and feel. The site will also allow for a more effective means of communicating with members while providing the public with information and developments in the local, regional and international shipping industry.
Scope
The website will highlight the history of the organisation inclusive of text and photographs. It will take visitors through the years from beginning to present. Information on the history of the shipping industry will also be included.
It will feature current articles on the organisation, its members and stakeholders in the shipping industry. Member information as well as pertinent details regarding the organisation’s subsidiaries will be documented for the website.
Information as it relates to shipping statistics, case studies, laws and regulations, international treaties and trade documents, shipping terms, careers in shipping, job opportunities, training opportunities, information for shippers including port listing and trade lanes will be main features of the content for the website.
The Association’s community involvement, industry calendar events and related links relevant industry members will also be featured.
Target Market
• The General Public;
• Members of the organization;
• Shipping Industry Stakeholders (local, regional and international);
• Tertiary students conducting research.
• Potential employees
• Potential Business Partners
Best Practice Bench Marketing
The following websites are being looked at:
• Korvel Quayworks - http://www.korvelquayworks.example/ (preferred look)
• Tessaly Maritime Association - http://www.tma-freight.example/ (like image transition on main page)
• Drovna - http://www.drovna.example (professional look)
• PLW - http://www.pelworth.example (preferred color: blue in logo)
• Quillo - http://www.quillo.example/electronics/tv-video-audio/ (preferred look for links page: image + short text below + visit site link)
Expected Result
• 3 - 5 pages which must include: [1] main page [2] standard page [3] links page

```html
<!DOCTYPE html>
<html lang="en">
<head>
<meta charset="utf-8">
<title>Contact Us – The Harbourline Shipping Association</title>
<link rel="stylesheet" href="https://fonts.googleapis.com/css2?family=Tinos&family=Questrial&family=Arimo:wght@400;700&display=swap">
<style>
:root{
  --navy:#0d2f8f;
  --brand:#1a56c9;
  --link:#2a6fe0;
  --ink:#222;
  --muted:#777;
  --line:#dcdcdc;
  --field:#cfd6e2;
  --bg-deep:#0a3aa6;
  --bg-light:#3b78e0;
  --white:#fff;
  --orange:#f07a1a;
}
*{box-sizing:border-box;margin:0;padding:0}
html,body{width:1200px;height:1027px;overflow:hidden}
body{
  font-family:"Arimo",Arial,sans-serif;font-size:11px;color:var(--ink);
  background:radial-gradient(ellipse at 50% 40%,var(--bg-light) 0%,var(--bg-deep) 60%,#08309a 100%);
  position:relative;
}
.page{position:absolute;left:195px;top:0;width:805px;height:973px;background:var(--white)}
.abs{position:absolute}
.site-name{left:118px;top:27px;font-family:"Tinos",serif;font-size:22px;color:var(--brand);display:flex;align-items:center;gap:10px}
.site-name .dot{position:absolute;left:-80px;top:-14px;width:58px;height:42px;border-radius:50%;background:var(--brand)}
.search{left:587px;top:34px;width:168px;height:19px;border:1px solid var(--line);background:#fafafa;font-size:9px;color:#aaa;font-style:italic;padding:4px 10px}
.search-btn{left:732px;top:34px;width:23px;height:19px;background:var(--brand)}
.nav{left:43px;top:70px;width:712px;height:31px;background:linear-gradient(#fff,#eef0f4);display:flex;align-items:center;font-family:"Questrial",sans-serif;font-size:9.5px;color:var(--navy)}
.nav span{padding:0 12px;border-right:1px solid #c9ccd6;line-height:13px}
.nav span:first-child{padding-left:20px}
.nav .active{margin-left:auto;border:0;background:var(--navy);color:#fff;width:86px;height:22px;display:flex;align-items:center;justify-content:center}
.banner{left:51px;top:114px;width:703px;height:123px;background:linear-gradient(100deg,#c9b79a 0%,#8f7e6c 35%,#6b6f7a 60%,#5f8a8c 100%);clip-path:polygon(0 0,100% 0,100% 75%,95% 100%,0 100%)}
.crumb{left:52px;top:244px;font-size:9px}
.crumb b{font-weight:400;color:var(--link)}
.rule{left:51px;top:261px;width:703px;height:1px;background:var(--line)}
h1{position:absolute;left:51px;top:278px;font-family:"Questrial",sans-serif;font-weight:400;font-size:13px;color:var(--navy)}
.addr,.reach{top:309px;line-height:15.5px;font-size:10.5px}
.addr{left:53px}.reach{left:317px}
.addr strong{color:var(--link)}
.dash{left:52px;top:379px;width:492px;border-top:1px dashed #bbb}
.map{left:48px;top:407px;width:234px;height:231px;background:linear-gradient(135deg,#e9e5dc,#d8d3c7);border:1px solid #ccc}
.routing{left:48px;top:660px;font-weight:700;color:var(--link)}
.label{font-size:10.5px}
.field{border:1px solid var(--field);border-radius:3px;background:#fff}
.btn{background:linear-gradient(#2f6fe0,#0d3fae);color:#fff;border-radius:3px;font-size:10.5px;display:flex;align-items:center;justify-content:center}
.select{font-size:10px;color:#999;font-style:italic;padding:6px 11px;display:flex;justify-content:space-between}
.code{left:318px;top:763px;font-size:16px;font-weight:700;color:var(--navy)}
.photo{left:571px;top:286px;width:184px;height:209px;background:linear-gradient(#b9c8d8 0%,#8b7460 55%,#6b5a4c 100%)}
.login{left:570px;top:512px;width:186px;height:53px;border:1px solid #ccc;display:flex;align-items:center}
.login .pic{width:60px;height:48px;margin-left:8px;background:linear-gradient(#e6e8ee,#b9bec9)}
.login span{margin-left:12px;font-family:"Questrial",sans-serif;font-size:13px;color:var(--navy)}
.social{top:591px;width:38px;height:24px;border-radius:4px;color:#fff;font-size:8px;display:flex;align-items:center;justify-content:center}
.partners{left:43px;top:869px;width:710px;height:74px;background:linear-gradient(90deg,#ececef,#fff 30%,#fff 70%,#ececef)}
.partners .title{position:absolute;left:5px;top:24px;font-family:"Questrial",sans-serif;font-size:13px;line-height:15px;color:var(--navy)}
.partner{position:absolute;top:27px;font-size:14px;font-weight:700;color:var(--navy);transform:translateX(-50%)}
.arrow{position:absolute;top:27px}
.footer-note{left:197px;top:991px;font-size:9px;color:#fff}
.footer-name{right:203px;top:986px;font-family:"Tinos",serif;font-size:17px;color:#fff;display:flex;align-items:center;gap:8px}
.footer-name i{width:12px;height:12px;border-radius:50%;background:#fff}
</style>
</head>
<body>
<main class="page">
  <div class="abs site-name"><span class="dot" aria-hidden="true"></span>The Harbourline Shipping Association</div>
  <div class="abs search">Search</div>
  <div class="abs search-btn"><svg width="23" height="19"><circle cx="11" cy="9" r="3.5" fill="none" stroke="#fff" stroke-width="1.6"/><line x1="13.5" y1="11.5" x2="16" y2="14" stroke="#fff" stroke-width="1.6"/></svg></div>
  <nav class="abs nav"><span>HOME</span><span>ABOUT US</span><span>PRODUCTS</span><span>SERVICES</span><span>NEWS</span><span>SUPPORT</span><span>PARTNERS</span><span style="border:0">CUSTOMERS</span><span class="active">CONTACT</span></nav>
  <div class="abs banner" role="img" aria-label="Aerial view of a container port with cranes and stacked containers"></div>
  <div class="abs crumb"><svg width="11" height="10" style="vertical-align:-1px"><path d="M5.5 0 11 5H9v5H6.5V7h-2v3H2V5H0z" fill="#2a6fe0"/></svg> &nbsp;Home &gt; <b>Contact Us</b></div>
  <div class="abs rule"></div>
  <h1>CONTACT US</h1>
  <div class="abs addr"><strong>The Harbourline Shipping Association</strong><br>12 Quayside Row, Eastmere Docks,<br>P.O. Box 4470, Port Avalen 7</div>
  <div class="abs reach">Tel: (555)310-4482-3, 310-7719-6<br>Fax:(555)310-4490<br>Email: info@harbourline-assoc.example</div>
  <div class="abs dash"></div>
  <div class="abs map" role="img" aria-label="Street map showing the association office location with an info bubble"></div>
  <div class="abs routing">Routing / driving directions:</div>
  <div class="abs label" style="left:48px;top:686px">Your postcode:</div>
  <div class="abs field" style="left:321px;top:680px;width:153px;height:27px;left:126px"></div>
  <div class="abs btn" style="left:49px;top:722px;width:89px;height:27px">Get directions</div>

  <div class="abs label" style="left:317px;top:406px">Name</div>
  <div class="abs field" style="left:315px;top:423px;width:225px;height:25px"></div>
  <div class="abs label" style="left:317px;top:459px">Phone</div>
  <div class="abs field" style="left:315px;top:477px;width:225px;height:25px"></div>
  <div class="abs label" style="left:316px;top:512px">E-mail Address</div>
  <div class="abs field" style="left:314px;top:530px;width:225px;height:25px"></div>
  <div class="abs label" style="left:316px;top:565px">Country</div>
  <div class="abs field select" style="left:314px;top:583px;width:225px;height:25px"><span>Avalen - AV</span><svg width="8" height="8"><path d="M0 2h8L4 7z" fill="#444"/></svg></div>
  <div class="abs label" style="left:316px;top:621px">Comment</div>
  <div class="abs field" style="left:313px;top:640px;width:225px;height:83px"></div>
  <div class="abs label" style="left:316px;top:740px">Please enter the code you see in this box:</div>
  <div class="abs code">K2347</div>
  <div class="abs field" style="left:391px;top:763px;width:154px;height:26px"></div>
  <div class="abs btn" style="left:313px;top:808px;width:77px;height:26px">Send</div>

  <div class="abs photo" role="img" aria-label="Straddle carrier vehicle at a container terminal"></div>
  <div class="abs login"><div class="pic" role="img" aria-label="Two port workers in hard hats reviewing plans"></div><span>MEMBER LOGIN</span></div>
  <div class="abs social" style="left:582px;background:#2d4c9a">Follow</div>
  <div class="abs social" style="left:640px;background:#1a9ad6">Post</div>
  <div class="abs social" style="left:696px;background:var(--orange)">Feed</div>

  <section class="abs partners">
    <div class="title">OUR<br>PARTNERS</div>
    <svg class="arrow" style="left:105px" width="12" height="20"><path d="M10 2 3 10l7 8" fill="none" stroke="#999" stroke-width="2.5"/></svg>
    <div class="partner" style="left:175px">Brinecrest</div>
    <div class="partner" style="left:321px">Osmund Wharves</div>
    <div class="partner" style="left:462px">Tidewell</div>
    <div class="partner" style="left:599px">Corvane Line</div>
    <svg class="arrow" style="left:687px" width="12" height="20"><path d="M2 2l7 8-7 8" fill="none" stroke="#999" stroke-width="2.5"/></svg>
  </section>
</main>
<div class="abs footer-note">© The Harbourline Shipping Association 2012, All Right Reserved</div>
<div class="abs footer-name"><i></i>The Harbourline Shipping Association</div>
</body>
</html>
```